Greeting Card Design - Bright Hearts Open Pages

Hi there

Thank you for taking the time to read about this project.

The project is for a range of greeting cards for the gay and lesbian community. The brand is called "Bright Hearts Open Pages".

In this project I require four designs in total (designs for homosexual couples, two for men and two for women). The designs need to reflect the general concept of being in love.

I am looking for variety (fun and funky, as well as modern and classy - please design to your tastes and I will give feedback).

I will work with each designer closely and provide the words for the cards as the designs are developed.

Thank you for considering this project.
Updates

I'm currently having issues with the craft huddle website and it won't let me upload files to show the logo. I will do so as soon as the website allows me. Thanks

Target Market(s)

Gay and lesbian community.

Industry/Entity Type

Community

Requirements
Must have
• I am looking for variety in the range. I would like designs that are modern and classy range; and also designs that are fun and funky.
Nice to have
• Hand drawings are good for the fun range, so is colour.
The classy range can be symbolic (e.g. holding hands) or black and whites.
Should not have
• Please do not use rainbows or rainbow coloured font.

```html
<!DOCTYPE html>
<html lang="en">
<head>
<meta charset="utf-8">
<title>Bright Hearts Open Pages – My love card</title>
<link href="https://fonts.googleapis.com/css2?family=Nothing+You+Could+Do&family=Montserrat:wght@700&display=swap" rel="stylesheet">
<style>
  :root {
    --paper: #ffffff;
    --line: #3a3a3a;
    --band-red: #be1e2d;
    --frame-taupe: #93857b;
    --ink: #2b2b2b;
    --photo-black: #262628;
    --photo-dark: #3a3a3c;
    --photo-mid: #7a7a7c;
    --photo-light: #d6d6d6;
    --photo-pale: #ededed;
    --dash: #8a8a8a;
  }
  * { margin: 0; padding: 0; box-sizing: border-box; }
  html, body {
    width: 807px; height: 1200px; overflow: hidden;
    background: var(--paper);
  }
  .canvas { position: relative; width: 807px; height: 1200px; }

  /* Outside of the card: back + cover */
  .card-outside {
    position: absolute; left: 23px; top: 25px; width: 762px; height: 553px;
    border: 1px solid var(--line); background: var(--paper);
  }
  .cover-photo {
    position: absolute; left: 381px; top: 0; width: 380px; height: 551px;
    background:
      /* embrace: shoulders and arms in pale tones */
      radial-gradient(ellipse 90px 70px at 40% 20%, var(--photo-light) 0%, transparent 100%),
      radial-gradient(ellipse 70px 160px at 88% 45%, var(--photo-pale) 0%, transparent 100%),
      radial-gradient(ellipse 60px 30px at 30% 8%, var(--photo-pale) 0%, transparent 100%),
      /* hands resting on the dress */
      radial-gradient(ellipse 70px 35px at 22% 75%, var(--photo-light) 0%, transparent 100%),
      radial-gradient(ellipse 60px 35px at 50% 82%, var(--photo-light) 0%, transparent 100%),
      radial-gradient(ellipse 55px 30px at 35% 98%, var(--photo-light) 0%, transparent 100%),
      radial-gradient(ellipse 40px 60px at 78% 88%, var(--photo-pale) 0%, transparent 100%),
      /* dark hair on the right */
      radial-gradient(ellipse 70px 160px at 68% 22%, var(--photo-black) 0%, transparent 100%),
      /* dark dress across the centre */
      linear-gradient(180deg, var(--photo-mid) 0%, var(--photo-dark) 30%, var(--photo-black) 50%, var(--photo-dark) 75%, var(--photo-black) 100%);
  }
  .cover-band {
    position: absolute; left: 381px; top: 257px; width: 232px; height: 72px;
    background: var(--band-red);
  }
  .cover-title {
    position: absolute; left: 421px; top: 257px;
    font-family: "Nothing You Could Do", cursive;
    font-size: 46px; line-height: 72px; color: var(--paper);
    white-space: nowrap;
  }
  .brand-badge {
    position: absolute; left: 610px; top: 241px; width: 96px; height: 96px;
    border-radius: 50%; background: var(--paper);
    display: flex; align-items: center; justify-content: center; text-align: center;
  }
  .brand-name {
    font-family: "Montserrat", sans-serif; font-weight: 700;
    font-size: 11px; line-height: 13px; color: var(--band-red);
    width: 72px;
  }

  /* Inside of the card */
  .card-inside {
    position: absolute; left: 23px; top: 631px; width: 762px; height: 556px;
    border: 16px solid var(--frame-taupe); background: var(--paper);
  }
  .fold-line {
    position: absolute; left: 405px; top: 631px; width: 0; height: 556px;
    border-left: 1px dashed var(--dash);
  }
  .inside-message {
    position: absolute; left: 420px; top: 792px; width: 350px;
    text-align: center;
    font-family: "Nothing You Could Do", cursive;
    font-size: 20px; line-height: 47px; color: var(--ink);
  }
</style>
</head>
<body>
<div class="canvas">
  <section class="card-outside">
    <div class="cover-photo" role="img" aria-label="Black and white posterised photograph of a couple in a close embrace, their hands resting together on a dark dress"></div>
    <div class="cover-band"></div>
    <div class="cover-title">My love...</div>
    <div class="brand-badge"><span class="brand-name">Bright Hearts Open Pages</span></div>
  </section>

  <section class="card-inside"></section>
  <div class="fold-line"></div>
  <p class="inside-message">Everything is better<br>with you by my side.<br>I love you</p>
</div>
</body>
</html>
```